Implant Denture Brochure

I would like to make a brochure to advertise implant dentures. This is for my dental clinic. I would like there to be some info about different implant denture options and advertise general cost. I like to use blue as a color and white. I may want to add or remove info based on the layout. Images of dentures with implants but no real photos just drawings or educational images. Real images of people smiling with dentures.

Upper
1. Implants for Upper Denture Implant Supported Removable $10,000 - $12,000 ( Includes fee for extraction of remaining upper teeth, in office sedation fees, Implant placement and necessary surgery of at least 4 implants, Does not include denture)
2. Upper Denture Implant Supported Fixed Bridge (Zirconia) $25,000 (Includes fee for extraction of all upper teeth, in office sedation fee, Implant placement and necessary surgery of at least 4 implants, includes temporary denture, and final denture)

Lower
1. Implants for Removable Lower Denture Implant Retained $5,000 - $7,000 (Includes fee for extraction of remaining lower teeth, in office sedation fees, Implant placement and necessary surgery of at least 2 implants, Does not include denture)

2. Implants for Removable Lower Denture Implant Supported $10,000 - $12,000 (Includes fee for extraction of remaining lower teeth, in office sedation fees, Implant placement and necessary surgery of at least 4 implants, Does not include denture)

3. Lower Denture Implant Supported Fixed Bridge (Zirconia) $25,000 (Includes fee for extraction of all upper teeth, in office sedation fee, Implant placement and necessary surgery of at least 4 implants, includes temporary denture, and final denture)

Copper Ridge Dental
#7 - 815 Lark Blvd N.
Copper Ridge, Alberta

```html
<!DOCTYPE html>
<html lang="en">
<head>
<meta charset="utf-8">
<title>Copper Ridge Dental – Implant Dentures</title>
<link rel="stylesheet" href="https://fonts.googleapis.com/css2?family=Bebas+Neue&family=Barlow+Semi+Condensed:wght@400;700&display=swap">
<style>
  :root {
    --indigo: #2b1c72;
    --blue: #1f73e6;
    --panel: #efefef;
    --paper: #ffffff;
    --ink: #1d1d24;
    --backdrop: #dedbd7;
  }
  * { margin: 0; padding: 0; box-sizing: border-box; }
  html, body { width: 1200px; height: 872px; overflow: hidden; }
  body { background: var(--backdrop); position: relative; font-family: "Barlow Semi Condensed", Arial, sans-serif; color: var(--ink); }

  .page { position: absolute; top: 62px; width: 529px; height: 749px; background: var(--paper); overflow: hidden; }
  .page--upper { left: 58px; }
  .page--lower { left: 613px; }

  .panel-shape { position: absolute; left: 0; top: 0; width: 529px; height: 749px; }

  .brand { position: absolute; left: 29px; top: 38px; display: flex; align-items: center; gap: 9px; }
  .brand__dot { width: 22px; height: 22px; border-radius: 50%; background: var(--ink); }
  .brand__name { font-family: "Bebas Neue", Arial, sans-serif; font-size: 25px; letter-spacing: 1.5px; color: var(--ink); line-height: 1; }

  .tagline { position: absolute; left: 29px; top: 119px; width: 190px; height: 45px; background: var(--indigo); border-radius: 4px;
    color: #fff; font-family: "Bebas Neue", Arial, sans-serif; font-size: 27px; letter-spacing: -0.5px; display: flex; align-items: center; justify-content: center; padding-top: 3px; }

  .headline { position: absolute; left: 29px; top: 176px; font-family: "Bebas Neue", Arial, sans-serif; font-size: 58px; line-height: 47px; letter-spacing: -1px; color: var(--indigo); }

  .hero-photo { position: absolute; left: 272px; top: 60px; width: 257px; height: 310px;
    background: radial-gradient(ellipse at 45% 45%, #e9d9c6 0%, #d8e3e0 45%, #9fd0c8 75%, #ffffff 100%); border-radius: 50% 0 0 0 / 40% 0 0 0; }

  .jaw-heading { position: absolute; font-family: "Bebas Neue", Arial, sans-serif; font-size: 34px; line-height: 1; color: var(--blue); letter-spacing: -0.5px;
    border-bottom: 2px solid var(--blue); padding-bottom: 1px; }

  .illustration { position: absolute; border-radius: 10px;
    background: linear-gradient(135deg, #f7b3aa 0%, #f08a80 45%, #2a86ee 46%, #4fa0f2 100%); }

  .option-title { position: absolute; font-weight: 700; font-size: 14.5px; line-height: 13.5px; color: var(--indigo); letter-spacing: -0.3px; }
  .option-body { position: absolute; font-size: 13.5px; line-height: 15.1px; letter-spacing: -0.2px; color: var(--ink); }

  .price { position: absolute; height: 41px; background: var(--indigo); border-radius: 4px; color: #fff;
    font-family: "Bebas Neue", Arial, sans-serif; font-size: 29px; letter-spacing: -0.5px; display: flex; align-items: center; justify-content: center; padding-top: 3px; }

  .address { position: absolute; left: 315px; top: 604px; width: 178px; height: 109px; background: var(--indigo); border-radius: 8px; padding: 6px; }
  .address__frame { width: 100%; height: 100%; border: 1px dashed rgba(255,255,255,0.8); border-radius: 5px; display: flex; flex-direction: column; align-items: center; justify-content: center; color: #fff; text-align: center; font-size: 13px; line-height: 15px; letter-spacing: -0.2px; }
  .address__pin { width: 11px; height: 15px; margin-bottom: 6px; }
</style>
</head>
<body>

<section class="page page--upper">
  <div class="hero-photo" role="img" aria-label="Photograph of a smiling senior couple embracing outdoors"></div>

  <svg class="panel-shape" viewBox="0 0 529 749" aria-hidden="true">
    <path d="M264 749 V400 C264 360 295 340 330 338 C365 336 395 362 428 372 C458 378 480 350 505 345 C520 345 529 360 529 380 V749 Z" fill="var(--panel)"/>
  </svg>

  <div class="brand"><span class="brand__dot"></span><span class="brand__name">Copper Ridge Dental</span></div>

  <div class="tagline">We Value Your Smile</div>
  <h1 class="headline">Your Copper<br>Ridge, AB<br>Dentist !</h1>

  <h2 class="jaw-heading" style="left:29px; top:345px;">Upper Jaw</h2>

  <div class="illustration" style="left:29px; top:392px; width:222px; height:106px;" role="img" aria-label="Illustration of an upper denture on four implants beside a blue tooth with implant parts"></div>
  <h3 class="option-title" style="left:29px; top:508px;">Denture<br>Implant Supported<br>Removable</h3>
  <p class="option-body" style="left:29px; top:557px; width:196px;">Implants for Upper Denture Implant Supported Removable Includes fee for extraction of remaining upper teeth, in office sedation fees, Implant placement and necessary surgery of atleast 4 implants, Does not include denture</p>
  <div class="price" style="left:29px; top:672px; width:161px;">$10,000 - $12,000</div>

  <div class="illustration" style="left:288px; top:392px; width:212px; height:106px;" role="img" aria-label="Illustration of a full upper and lower fixed bridge on implants beside a blue tooth with implant"></div>
  <h3 class="option-title" style="left:288px; top:508px;">Upper Implant<br>Supported Full Arch<br>Fixed Bridge</h3>
  <p class="option-body" style="left:288px; top:557px; width:205px;">Upper Denture Implant Supported Fixed Bridge (Zirconia) Includes fee for extraction of all upper teeth, in office sedation fee, Implant placement and necessary surgery of at least 4 implants, includes temporary denture, and final denture</p>
  <div class="price" style="left:288px; top:672px; width:87px;">$25,000</div>
</section>

<section class="page page--lower">
  <svg class="panel-shape" viewBox="0 0 529 749" aria-hidden="true">
    <path d="M0 0 H265 V370 C265 420 240 440 210 440 C190 440 175 425 160 420 C150 415 140 418 130 425 C105 440 80 445 55 438 C20 428 0 400 0 370 Z" fill="var(--panel)"/>
  </svg>

  <h2 class="jaw-heading" style="left:41px; top:33px;">Lower Jaw</h2>

  <div class="illustration" style="left:33px; top:81px; width:98px; height:120px;" role="img" aria-label="Illustration of a lower denture retained by two implants with bar"></div>
  <h3 class="option-title" style="left:41px; top:214px;">Removable Lower<br>Denture Implant Retained</h3>
  <p class="option-body" style="left:41px; top:246px; width:200px;">Implants for Removable Lower Denture Implant Retained Includes fee for extraction of remaining lower teeth, in office sedation fees, Implant placement and necessary surgery of at least 2 implants, Does not include denture)</p>
  <div class="price" style="left:41px; top:359px; width:161px;">$5,000 - $7,000</div>

  <div class="illustration" style="left:305px; top:81px; width:110px; height:120px;" role="img" aria-label="Illustration of a lower denture supported by four implants"></div>
  <h3 class="option-title" style="left:309px; top:214px;">Removable Lower<br>Denture Implant Supported</h3>
  <p class="option-body" style="left:309px; top:246px; width:196px;">Implants for Removable Lower Denture Implant Supported Includes fee for extraction of remaining lower teeth, in office sedation fees, Implant placement and necessary surgery of at least 4 implants, Does not include denture)</p>
  <div class="price" style="left:309px; top:359px; width:161px;">$10,000 - $12,000</div>

  <div class="illustration" style="left:165px; top:428px; width:90px; height:122px;" role="img" aria-label="Illustration of upper and lower full arch bridges separated above implants"></div>
  <h3 class="option-title" style="left:41px; top:506px;">Lower Implant<br>Supported Full Arch<br>Fixed Bridge</h3>
  <p class="option-body" style="left:41px; top:557px; width:212px;">Lower Denture Implant Supported Fixed Bridge (Zirconia) Includes fee for extraction of all upper teeth, in office sedation fee, Implant placement and necessary surgery of at least 4 implants, includes temporary denture, and final denture)</p>
  <div class="price" style="left:41px; top:672px; width:87px;">$25,000</div>

  <div class="illustration" style="left:332px; top:462px; width:138px; height:118px; background: radial-gradient(ellipse at 50% 55%, #f4a79e 0%, #f08a80 55%, #ffffff 100%);" role="img" aria-label="Illustration of a lower jaw model with a single implant crown"></div>

  <div class="address">
    <div class="address__frame">
      <svg class="address__pin" viewBox="0 0 12 16" aria-hidden="true"><path d="M6 0C2.7 0 0 2.6 0 5.9 0 10.3 6 16 6 16s6-5.7 6-10.1C12 2.6 9.3 0 6 0zm0 8.2a2.3 2.3 0 1 1 0-4.6 2.3 2.3 0 0 1 0 4.6z" fill="#fff"/></svg>
      <span>Copper Ridge Dental</span>
      <span>#7 - 815 Lark Blvd N.</span>
      <span>Copper Ridge, Alberta</span>
    </div>
  </div>
</section>

</body>
</html>
```